Website Header Development

I am after a redesign of the Header of a website www.tlvoltaris.com.au.
This project is for the header only, and should fit in with the rest of the site
Target Market(s)
Business
Requirements
Should not have
- Over the top. Keep it simple

```html
<!DOCTYPE html>
<html lang="en">
<head>
<meta charset="utf-8">
<title>Voltaris Energy – Resource Efficiency</title>
<link href="https://fonts.googleapis.com/css2?family=Alegreya:wght@700&family=Hind:wght@400;600&display=swap" rel="stylesheet">
<style>
:root{
  --brand-blue:#1f3f8f;
  --heading-blue:#0e1f7a;
  --nav-green:#23803c;
  --nav-green-dark:#176b30;
  --text-dark:#1a1a1a;
  --text-grey:#6a6a6a;
  --field-border:#b9b9b9;
  --sky:#bfe3f2;
  --leaf:#9fd17a;
}
*{box-sizing:border-box;margin:0;padding:0}
html,body{width:1200px;height:1007px;overflow:hidden;background:#fff}
body{position:relative;font-family:'Hind',sans-serif;color:var(--text-dark)}

.site-header{position:absolute;left:0;top:0;width:1200px;height:140px;
  background:
    radial-gradient(ellipse 260px 90px at 950px 70px, rgba(31,120,170,.55), transparent 70%),
    radial-gradient(ellipse 220px 80px at 1120px 40px, rgba(159,209,122,.7), transparent 70%),
    radial-gradient(ellipse 300px 110px at 750px 40px, rgba(191,227,242,.8), transparent 70%),
    radial-gradient(ellipse 300px 80px at 200px 130px, rgba(240,240,200,.6), transparent 70%),
    linear-gradient(#f7fbfd,#eef6f8);}
.brand{position:absolute;left:56px;top:58px;display:flex;align-items:center;gap:12px}
.brand-name{font-family:'Hind',sans-serif;font-weight:600;font-size:40px;line-height:1;color:var(--brand-blue)}
.brand-mark{width:26px;height:26px;background:var(--brand-blue)}

.main-nav{position:absolute;left:0;top:140px;width:1200px;height:63px;
  background:linear-gradient(90deg,var(--nav-green) 0%,var(--nav-green) 88%,var(--nav-green-dark) 100%)}
.main-nav a{position:absolute;color:#fff;text-decoration:none;font-size:14px;top:15px}
.main-nav a.major{font-size:17px;font-weight:600;top:20px}

.page-title{position:absolute;left:73px;width:700px;top:238px;text-align:center;
  font-family:'Alegreya',serif;font-weight:700;font-size:29px;color:var(--heading-blue)}
.copy{position:absolute;left:73px;font-size:17px;line-height:30px}
.copy.narrow{width:240px}
.copy.wide{width:700px}
.copy.muted{color:var(--text-grey)}
.bullets{position:absolute;left:104px;top:905px;list-style:none;font-size:17px;line-height:30px;color:var(--text-grey)}
.bullets li{position:relative;padding-left:16px}
.bullets li::before{content:"";position:absolute;left:0;top:12px;width:6px;height:6px;background:#555}
.clip{position:absolute;left:0;top:985px;width:800px;height:22px;overflow:hidden}
.clip .copy{top:12px}

.hero-photo{position:absolute;left:347px;top:313px;width:420px;height:280px;
  background:radial-gradient(ellipse 200px 180px at 65% 45%, #d9c3b4, transparent 70%),
    linear-gradient(135deg,#f4f4f4,#e6e6e6 60%,#dcdfe3)}

.search{position:absolute;left:885px;top:205px;width:220px;height:36px;border:1px solid #d6d6d6;border-radius:3px;
  display:flex;align-items:center;padding-left:10px;gap:8px;color:#999;font-size:16px}
.sidebar-title{position:absolute;left:885px;top:282px;width:230px;font-family:'Alegreya',serif;font-weight:700;
  font-size:26px;line-height:36px;letter-spacing:2px;color:var(--brand-blue)}
.form-note{position:absolute;left:885px;width:230px;font-size:12.5px;font-weight:600;line-height:30px}
.field{position:absolute;left:885px;width:211px;height:34px;border:1px solid var(--field-border);background:#fff}
</style>
</head>
<body>
<header class="site-header">
  <div class="brand"><span class="brand-name">voltaris energy</span><span class="brand-mark"></span></div>
</header>
<nav class="main-nav">
  <a class="major" href="#" style="left:102px">Home</a>
  <a href="#" style="left:192px">About Us</a>
  <a href="#" style="left:287px">Services</a>
  <a href="#" style="left:373px">Projects and Case Studies</a>
  <a class="major" href="#" style="left:568px">Financial Information</a>
  <a href="#" style="left:780px">News</a>
  <a href="#" style="left:851px">Contact</a>
</nav>

<main>
  <h1 class="page-title">Resource Efficiency – Sustainable Solutions</h1>
  <p class="copy narrow" style="top:298px">Is your business performing as well as your competitors?</p>
  <p class="copy narrow" style="top:389px">Are your fixed costs comparable to industry leaders?</p>
  <p class="copy narrow" style="top:510px">Is your business becoming less profitable with increased energy, waste and water prices?</p>
  <div class="hero-photo" role="img" aria-label="Photo of a businessman holding a puzzle piece over a sketched 'Solution' jigsaw"></div>
  <p class="copy wide" style="top:631px">Do you wish to reduce your impact on the environment through reducing the use of resources (energy, waste and water) within your business?</p>
  <p class="copy wide muted" style="top:722px">If so, Voltaris can assist your business to achieve its core functions in the most effective manner.</p>
  <p class="copy wide muted" style="top:813px">Voltaris can assist your business in achieving improved productivity through the implementation of:</p>
  <ul class="bullets">
    <li>innovative and targeted resource efficiency strategies</li>
    <li>streamlined business strategies</li>
  </ul>
  <div class="clip"><p class="copy wide">It is also about helping your staff work more efficiently and sustainably.</p></div>
</main>

<aside>
  <div class="search">
    <svg width="16" height="16" viewBox="0 0 16 16"><circle cx="6.5" cy="6.5" r="5" fill="none" stroke="#888" stroke-width="2"/><line x1="10" y1="10" x2="15" y2="15" stroke="#888" stroke-width="2"/></svg>
    Search
  </div>
  <h2 class="sidebar-title">Voltaris Energy Newsletter</h2>
  <p class="form-note" style="top:415px">Would you like to receive our regular monthly Newsletter? Please fill in your Name:</p>
  <div class="field" style="top:515px"></div>
  <p class="form-note" style="top:565px">Let us know your email address so we can send the Newsletter directly to your email address. (Note that your details will not be passed onto any 3rd parties. Your details stricly remain with Voltaris Energy for the purposes of sending you the Voltaris Energy Newsletter)</p>
  <div class="field" style="top:816px"></div>
  <p class="form-note" style="top:865px">Further, please let us know if there are particular topics you would like to hear about in our Newsletters</p>
  <div class="field" style="top:966px;width:232px;height:60px"></div>
</aside>
</body>
</html>
```